hello! I need a very simple modern business card for a new venture called The Quiet Harbour Retreats. It's the very first Tech-Free retreat in Asia!

The concept is very unique. Basically a group of 12-15 people would go on a 3 to 4 days retreat where no phone or internet is allowed. The first retreat will take place in a beautiful villa in Bali by the sea. It will include yoga, meditation, art & writing workshops, swimming, hiking, cooking, healthy vegetarian meals, etc.

Reason: Thanks for your submissions. I still haven't found exactly what I'm after but the designs that haven't be eliminated are getting close.. Please keep in mind that it should be a simple, modern and upmarket business card. Thanks

Target Market(s)

Both men and women who would like to disconnect from life, computer and phone for 3/4 days. They can be either local or expats but based in Asia (Singapore, Hong Kong).
Client will have to pay for their own flight and then the price is around US$600 for a 3-day retreat including everything (accommodation, food, activities). It means clients already have a good income. They are usually working in marketing, advertising, digital media, public relations.

Industry/Entity Type

Internet

Font styles to use
Other font styles liked:
• anything modern you like

Colors
acd036
9bcb3c
f37022
f68d4d
1b1b1b
333333
acd037

Requirements
Must have
• Name: Rell Vonta
Position: #screenwanderer
Company: The Quiet Harbour Retreats (asia should be smaller than the rest)
- Email button - quietharbourretreats@mailora.com
- Facebook button - www.pagenook.com/quietharbourretreats
- Eventbrite button - www.quietharbourretreats.ticketvale.com
Nice to have
• You can use my logo attached but it's something I designed quickly on Power Point so it would be nice to include your own version.
Should not have
• anything tacky or girly or childish. thanks

```html
<!DOCTYPE html>
<html lang="en">
<head>
<meta charset="utf-8">
<title>The Quiet Harbour Retreats – Business Cards</title>
<link rel="stylesheet" href="https://fonts.googleapis.com/css2?family=Josefin+Sans:wght@300;400;600&display=swap">
<style>
  :root {
    --backdrop: #c8c8c8;
    --orange: #eb6e2c;
    --orange-soft: #f68d4d;
    --green: #9bcb3c;
    --white: #ffffff;
    --ink: #333333;
    --ink-dark: #1b1b1b;
  }
  * { margin: 0; padding: 0; box-sizing: border-box; }
  html, body {
    width: 1200px;
    height: 1000px;
    overflow: hidden;
    background: var(--backdrop);
    font-family: "Josefin Sans", Arial, sans-serif;
  }
  .sheet { position: relative; width: 1200px; height: 1000px; }

  .card {
    position: absolute;
    width: 340px;
    height: 194px;
    overflow: hidden;
  }
  .card--col1 { left: 31px; }
  .card--col2 { left: 428px; }
  .card--col3 { left: 828px; }
  .card--row1 { top: 282px; }
  .card--row2 { top: 531px; }

  /* Front */
  .card--front { background: var(--orange); }
  .front-mark {
    position: absolute;
    left: 0;
    right: 0;
    top: 0;
    bottom: 0;
    display: flex;
    align-items: center;
    justify-content: center;
    gap: 14px;
  }
  .front-mark__dot {
    width: 30px;
    height: 30px;
    border-radius: 50%;
    background: var(--green);
    flex: none;
  }
  .front-mark__name {
    color: var(--white);
    font-weight: 600;
    font-size: 22px;
    line-height: 1.05;
    text-transform: uppercase;
    letter-spacing: 0.2px;
  }

  /* Back */
  .card--back { background: var(--white); }
  .back-mark {
    position: absolute;
    left: 19px;
    top: 22px;
    color: var(--orange);
    font-weight: 600;
    font-size: 19px;
    line-height: 1.05;
    text-transform: uppercase;
  }
  .person {
    position: absolute;
    right: 28px;
    top: 62px;
    text-align: right;
  }
  .person__name {
    color: var(--orange);
    font-weight: 600;
    font-size: 14px;
    font-variant: small-caps;
    letter-spacing: 0.6px;
  }
  .person__handle {
    color: var(--ink);
    font-size: 10.5px;
    margin-top: 2px;
  }
  .contacts {
    position: absolute;
    right: 27px;
    top: 116px;
    list-style: none;
  }
  .contacts__item {
    display: flex;
    justify-content: flex-end;
    align-items: center;
    gap: 6px;
    height: 18px;
    color: var(--ink);
    font-size: 10.5px;
  }
  .contacts__icon {
    width: 13px;
    height: 13px;
    flex: none;
    display: block;
  }
  .contacts__icon--page { background: #3b5a9a; border-radius: 2px; }
  .contacts__icon--tickets { background: var(--orange); border-radius: 2px; }
</style>
</head>
<body>
<main class="sheet">
  <section class="card card--front card--col1 card--row1">
    <div class="front-mark"><span class="front-mark__dot"></span><p class="front-mark__name">The Quiet Harbour<br>Retreats</p></div>
  </section>
  <section class="card card--front card--col2 card--row1">
    <div class="front-mark"><span class="front-mark__dot"></span><p class="front-mark__name">The Quiet Harbour<br>Retreats</p></div>
  </section>
  <section class="card card--front card--col3 card--row1">
    <div class="front-mark"><span class="front-mark__dot"></span><p class="front-mark__name">The Quiet Harbour<br>Retreats</p></div>
  </section>
  <section class="card card--front card--col1 card--row2">
    <div class="front-mark"><span class="front-mark__dot"></span><p class="front-mark__name">The Quiet Harbour<br>Retreats</p></div>
  </section>
  <section class="card card--front card--col2 card--row2">
    <div class="front-mark"><span class="front-mark__dot"></span><p class="front-mark__name">The Quiet Harbour<br>Retreats</p></div>
  </section>

  <section class="card card--back card--col3 card--row2">
    <p class="back-mark">The Quiet<br>Harbour<br>Retreats</p>
    <div class="person">
      <p class="person__name">Rell Vonta</p>
      <p class="person__handle">#screenwanderer</p>
    </div>
    <ul class="contacts">
      <li class="contacts__item">quietharbourretreats@mailora.com
        <svg class="contacts__icon" viewBox="0 0 13 13" aria-hidden="true">
          <rect width="13" height="13" rx="2" fill="#9bcb3c"/>
          <rect x="2" y="3.5" width="9" height="6" fill="#ffffff"/>
          <path d="M2 3.5 L6.5 7 L11 3.5" fill="none" stroke="#9bcb3c" stroke-width="1"/>
        </svg>
      </li>
      <li class="contacts__item">www.pagenook.com/quietharbourretreats<span class="contacts__icon contacts__icon--page"></span></li>
      <li class="contacts__item">www.quietharbourretreats.ticketvale.com<span class="contacts__icon contacts__icon--tickets"></span></li>
    </ul>
  </section>
</main>
</body>
</html>
```